International Clinical Software Company needs a new business card design

We are looking for a new business card design for our company that has recently expanded into the UK market, making us a multinational company.
After having rebranded our website and produced a new style guide, we are looking for a business card that is creative and attention grabbing, while being consistent with the style and colour scheme used on the new website, www.plumvora.example
We produce care management technology for the aged care market, but the main aspect we aim to communicate is the human element of our software, and the way it assists in providing better care for aged people, and stronger relationships between aged people and the staff that care for them.
Our current business card is a dark green with gold text, which makes the text quite difficult to read, not very aesthetically appealing and the colour scheme looks quite dated.
We would like something fresh and modern, that can still be colourful but doesn't use large blocks of dark colour, and uses the colours within our logo.
Something tying in with the leaves that are used in our logo could work quite nicely, along with the Autumn/Fall colours of soft greens, yellows and reds (also in our existing logo). However also happy to look at fresh, completely out of the box ideas we may not have yet considered.
Target Market(s)
The people that receive this business card work in the aged card or health industry and are either corporate/management level staff or clinical (Registered Nurses, care workers etc.)
Industry/Entity Type
Health Product
Contact Information for Business Card
Company Name - BrindlewayCare
Company locations: United Kingdom, Australia, New Zealand
Staff Details:
Staff name: Derek Mallow
Staff job title: Executive Chairman
Staff email: d.mallow@plumvora.example
Office phone number: 01742 918576
Font styles to use
Other font styles liked:
- Calibri
Requirements
Must have
- Must include the BrindlewayCare brand name in it's current font
- Must include logo (3 leaves in gold circle)
- Must include Business Card Details
Nice to have
- Elements of gold
- White space
- Something autumn themed but not too cliched
Should not have
- No blue - used by a major competitor and we would like to differentiate from them
- Large blocks of dark green colour (the green that appears in our leaves on the logo on our current business card is the background colour and it is far too dark)

```html
<!DOCTYPE html>
<html lang="en">
<head>
<meta charset="utf-8">
<title>BrindlewayCare – Business Card</title>
<link rel="stylesheet" href="https://fonts.googleapis.com/css2?family=Open+Sans:wght@300;400;600;700&display=swap">
<style>
  :root {
    --page-bg: #e9e4dc;
    --crimson: #b0103f;
    --crimson-dark: #8f0c33;
    --taupe: #a9998a;
    --white: #ffffff;
    --leaf-yellow: #f3d34a;
    --leaf-gold: #f0b530;
    --leaf-orange: #e77a22;
    --leaf-red: #c8461c;
    --leaf-pale: #f3eaa0;
  }
  * { box-sizing: border-box; margin: 0; padding: 0; }
  html, body {
    width: 1200px; height: 950px; overflow: hidden;
    background: var(--page-bg);
    font-family: "Open Sans", Calibri, Arial, sans-serif;
  }
  .sheet {
    width: 1200px; height: 950px;
    display: flex; flex-direction: column; align-items: center; justify-content: center;
    gap: 50px;
  }
  .card {
    position: relative;
    width: 700px; height: 400px;
    border-radius: 22px;
    overflow: hidden;
    box-shadow: 0 8px 24px rgba(60, 40, 20, 0.18);
  }
  /* Front */
  .card-front__photo {
    position: absolute; inset: 0;
    background:
      radial-gradient(circle at 8% 20%, var(--leaf-red) 0, rgba(200,70,28,0) 30%),
      radial-gradient(circle at 30% 85%, var(--leaf-orange) 0, rgba(231,122,34,0) 35%),
      radial-gradient(circle at 85% 85%, var(--leaf-gold) 0, rgba(240,181,48,0) 40%),
      radial-gradient(circle at 20% 0%, var(--leaf-orange) 0, rgba(231,122,34,0) 30%),
      linear-gradient(110deg, var(--leaf-gold) 0%, var(--leaf-yellow) 40%, var(--leaf-pale) 75%, var(--leaf-yellow) 100%);
  }
  .brand-panel {
    position: absolute; left: 0; top: 0; bottom: 0;
    width: 270px;
    background: var(--white);
    border-radius: 0 22px 22px 0;
    display: flex; flex-direction: column; align-items: center; justify-content: center;
    gap: 22px;
  }
  .brand-panel__mark {
    width: 86px; height: 86px; border-radius: 50%;
    background: var(--taupe);
  }
  .brand-panel__name {
    font-weight: 300; font-size: 30px; color: var(--taupe);
    letter-spacing: 0.5px;
  }
  .contact {
    position: absolute; left: 330px; top: 62px;
    color: var(--crimson);
  }
  .contact__name { font-size: 30px; font-weight: 700; line-height: 1.15; }
  .contact__title { font-size: 20px; font-weight: 400; margin-bottom: 18px; }
  .contact__regions { font-size: 19px; line-height: 1.3; margin-bottom: 16px; }
  .contact__list { list-style: none; font-size: 18px; line-height: 1.55; }
  .contact__item { display: flex; align-items: center; gap: 10px; }
  .contact__icon { width: 18px; height: 18px; flex: none; }
  /* Back */
  .card-back { background: var(--crimson); }
</style>
</head>
<body>
<main class="sheet">
  <section class="card card-front" aria-label="Business card front">
    <div class="card-front__photo" role="img" aria-label="Photograph of golden and orange autumn maple leaves"></div>
    <div class="brand-panel">
      <div class="brand-panel__mark" aria-hidden="true"></div>
      <div class="brand-panel__name">BrindlewayCare</div>
    </div>
    <div class="contact">
      <div class="contact__name">Derek Mallow</div>
      <div class="contact__title">Executive Chairman</div>
      <div class="contact__regions">United Kingdom,<br>Australia, New Zealand</div>
      <ul class="contact__list">
        <li class="contact__item">
          <svg class="contact__icon" viewBox="0 0 20 20" aria-hidden="true"><path fill="#b0103f" d="M5 2l3 4-2 2c1 2.5 3.5 5 6 6l2-2 4 3-2 3C8 18 2 12 2 4z"/></svg>
          01742 918576
        </li>
        <li class="contact__item">
          <svg class="contact__icon" viewBox="0 0 20 20" aria-hidden="true"><rect x="1" y="4" width="18" height="12" rx="2" fill="#b0103f"/><path d="M2 5l8 6 8-6" fill="none" stroke="#fff" stroke-width="1.5"/></svg>
          d.mallow@plumvora.example
        </li>
        <li class="contact__item">
          <svg class="contact__icon" viewBox="0 0 20 20" aria-hidden="true"><circle cx="10" cy="10" r="9" fill="#b0103f"/><path d="M1 10h18M10 1c-4 4-4 14 0 18M10 1c4 4 4 14 0 18" fill="none" stroke="#fff" stroke-width="1.2"/></svg>
          www.plumvora.example
        </li>
      </ul>
    </div>
  </section>
  <section class="card card-back" aria-label="Business card back"></section>
</main>
</body>
</html>
```